Children’s entertainer/balloon artist Website Home Page and custom landing page

I need a home page design for the home page of a children and family entertainer/balloon twister’s website. I also need a custom landing page for family theatre shows performed by the same entertainer.
It will be a Wordpress website and I need the final artwork in a layer Photoshop file with all the layers clearly named and labeled.

Target Market(s)

The site visitors are mainly mums, aged between early 20’s and late 30’s. Other visitors will included companies for Christmas functions, and event organisers for corporate functions.

Industry/Entity Type

Entertainment

Number of Pages Required

2 page

Font styles to use
Sans Serif

Colors
34a6d7
f37122

Requirements
Must have
• Layout
• I have included a wireframe for the home page layout and the custom landing page for your reference. This is a guide only and I welcome your interpretation with the rough layout provided.
• This website needs to look good on all devices as it will be fully responsive.
• It needs to include a footer area on the page, that has social media and a call to action area included.
• Colours
• The main colours for the site is:
• orange (call to action colour)
• ff6800
• blue/turquoise
• 42abc3
• Pictures
• I have included images of the entertainer/balloon artist for you to use/take inspiration from.
• These images will be included on the website. I want to show lots of people having fun.
• I would like to have elements of the logo used in isolation across the website
• i.e. the octopus figure to be included in the footer or the bird element to be included in the testimonial slider etc.
• Elements to include
• Note: use the images of the entertainer in the boxes on the home page (balloon shows, balloon twisting, balloon workshops, theatre shows (the three little balloon pigs on his head)
Nice to have
Should not have
• Element to avoid
• Stock imagery of balloon sculptures - use images provided.

```html
<!DOCTYPE html>
<html lang="en">
<head>
<meta charset="utf-8">
<title>Benny Fairweather – Children's Entertainer</title>
<link href="https://fonts.googleapis.com/css2?family=Lobster+Two:ital,wght@1,700&family=Open+Sans:wght@400;600;700&display=swap" rel="stylesheet">
<style>
:root{
  --blue:#34a6d7;
  --blue-dark:#2288bd;
  --blue-light:#5cc0e8;
  --orange:#f37122;
  --orange-dark:#dc5e12;
  --navy:#1d2c66;
  --ink:#3c3c3c;
  --grey:#8a8a8a;
  --line:#e2e2e2;
  --paper:#ffffff;
  --head:'Lobster Two', cursive;
  --body:'Open Sans', sans-serif;
}
*{box-sizing:border-box;margin:0;padding:0}
html,body{width:683px;height:1200px;overflow:hidden;background:var(--paper)}
body{font-family:var(--body);color:var(--ink);font-size:7px;line-height:1.5}
.page{position:relative;width:683px;height:1200px;overflow:hidden}
.abs{position:absolute}
.btn{display:inline-block;background:var(--orange);color:#fff;font-family:var(--body);font-weight:700;font-size:6.5px;padding:4px 10px;border-radius:10px}

/* header */
.site-header{left:0;top:0;width:683px;height:100px;background:radial-gradient(ellipse at 50% 0%,var(--blue-light),var(--blue) 60%,var(--blue-dark))}
.brand{left:0;top:14px;width:683px;display:flex;justify-content:center;align-items:center;gap:6px}
.brand-dot{width:22px;height:22px;border-radius:50%;background:var(--orange)}
.brand-name{font-family:var(--head);font-size:20px;color:#fff}
.main-nav{left:0;top:58px;width:683px;height:40px}
.main-nav svg{position:absolute;left:0;top:0}
.nav-list{position:absolute;left:88px;top:13px;display:flex;gap:34px;list-style:none;font-family:var(--head);color:#fff;font-size:10px}
.nav-list .current{border:1.5px solid #fff;border-radius:50%;padding:1px 9px;margin-top:-3px}

/* hero */
.hero{left:0;top:98px;width:683px;height:314px}
.hero-photo{position:absolute;inset:0;background:linear-gradient(100deg,#243a88 0%,var(--navy) 45%,#2f54a8 100%)}
.hero-copy{position:absolute;left:430px;top:115px;width:200px;text-align:right;color:#fff}
.hero-copy h1{font-family:var(--head);font-size:22px;line-height:1.1}
.hero-copy h1 span{color:var(--orange)}
.hero-copy p{font-style:italic;font-size:7.5px;margin:6px 0 10px 40px}
.dots{position:absolute;left:326px;top:294px;display:flex;gap:4px}
.dots i{width:5px;height:5px;border-radius:50%;background:#fff;opacity:.6}
.dots i:first-child{opacity:1;background:var(--orange)}

/* testimonial */
.testimonial{left:91px;top:426px;width:360px;height:96px;border:1px solid var(--line);background:#fafafa;padding:10px 14px}
.section-title{font-family:var(--head);font-size:11px;color:var(--ink)}
.testimonial p{font-style:italic;color:var(--grey);font-size:6.3px;margin-top:6px}
.testimonial .author{color:var(--blue);font-style:italic;margin-top:4px}
.arrows{position:absolute;right:12px;top:10px;display:flex;gap:3px}
.arrows span{width:10px;height:10px;border-radius:50%;background:var(--orange)}
.call-box{left:465px;top:426px;width:128px;height:96px;background:var(--orange);color:#fff;text-align:center;padding:10px 6px}
.call-box small{font-size:6px}
.call-box h3{font-family:var(--head);font-size:13px;line-height:1.1}
.call-box .phone{font-weight:700;font-size:11px;margin:2px 0 5px}
.call-box .btn-line{display:inline-block;border:1px solid #fff;border-radius:10px;font-weight:700;font-size:6.5px;padding:3px 10px}

/* welcome */
.welcome-title{left:91px;top:540px}
.welcome-photo{left:91px;top:565px;width:196px;height:122px;background:linear-gradient(135deg,#f4b6c4,#e98aa5 55%,#c5e0ef)}
.welcome-text{left:300px;top:562px;width:152px}
.welcome-text h2{font-family:var(--head);color:var(--orange);font-size:9.5px;line-height:1.25}
.welcome-text p{color:var(--grey);font-size:6px;margin:6px 0}
.news{left:465px;top:535px;width:128px}
.news-item{display:flex;gap:5px;margin-top:8px}
.news-thumb{width:30px;height:24px;flex:none}
.news-item p{font-size:5.8px;color:var(--grey);line-height:1.35}
.news-item b{display:block;color:var(--blue);font-size:6px}

/* services */
.services{left:0;top:705px;width:683px;height:245px;background:radial-gradient(ellipse at 50% 40%,var(--blue-light),var(--blue) 65%,var(--blue-dark))}
.cards{position:absolute;left:91px;top:22px;display:flex;gap:13px}
.card{width:115px;height:200px;background:#fff}
.card h3{background:var(--orange);color:#fff;font-family:var(--head);font-size:10px;padding:5px 8px;height:24px}
.card-photo{height:80px}
.card p{color:var(--grey);font-size:6px;padding:7px 8px 6px}
.card .btn{margin-left:8px}

/* connect */
.connect{left:0;top:960px;width:683px;text-align:center}
.connect h2{font-family:var(--head);font-size:12px}
.connect p{color:var(--grey);font-size:6px;width:260px;margin:4px auto 0}
.signup{position:absolute;left:176px;top:66px;width:330px;height:26px;display:flex;align-items:center}
.signup .icon{width:26px;height:26px;border-radius:50%;background:var(--orange);display:flex;align-items:center;justify-content:center}
.signup .field{flex:1;height:18px;margin:0 6px;border:1px solid var(--line);text-align:left;color:var(--grey);font-size:6px;padding:3px 8px}
.signup .go{width:20px;height:20px;background:var(--orange);color:#fff;font-weight:700;font-size:7px;display:flex;align-items:center;justify-content:center}

/* footer */
.site-footer{left:0;top:1080px;width:683px;height:120px;background:var(--orange);color:#fff;text-align:center}
.site-footer svg{position:absolute;left:0;top:-10px}
.social{position:relative;display:flex;justify-content:center;gap:6px;padding-top:20px}
.social span{width:14px;height:14px;border-radius:50%;border:1.5px solid #fff}
.footer-links{position:relative;font-size:6px;margin-top:10px}
.copyright{position:relative;font-size:5.5px;opacity:.85;margin-top:3px}
</style>
</head>
<body>
<div class="page">

  <header class="site-header abs">
    <div class="brand abs"><span class="brand-dot"></span><span class="brand-name">Twistle Parties</span></div>
    <nav class="main-nav abs">
      <svg width="683" height="40" viewBox="0 0 683 40"><path d="M0 8 Q341 -6 683 8 L683 40 L0 40 Z" fill="#f37122"/></svg>
      <ul class="nav-list">
        <li class="current">Home</li><li>Balloon Shows</li><li>Balloon Twisting</li><li>Theatre</li><li>Reviews</li><li>Contact</li>
      </ul>
    </nav>
  </header>

  <section class="hero abs">
    <div class="hero-photo" role="img" aria-label="Entertainer wearing colourful balloon sculptures against a dark blue backdrop"></div>
    <div class="hero-copy">
      <h1>Benny <span>Fairweather</span></h1>
      <p>Sed ut perspiciatis unde omnis iste natus error sit voluptatem accusantium doloremque laudan.</p>
      <span class="btn">Read More</span>
    </div>
    <div class="dots"><i></i><i></i><i></i><i></i></div>
  </section>

  <section class="testimonial abs">
    <h2 class="section-title">Testimonial</h2>
    <div class="arrows"><span></span><span></span></div>
    <p>“ Sed ut perspiciatis unde omnis iste natus error sit voluptatem accusantium doloremque laudantium, totam rem aperiam eaque ipsa quae ab illo inventore veritatis et quasi architecto beatae vitae dicta sunt explicabo. Nemo enim ipsam voluptatem quia voluptas sit aspernatur aut odit aut fugit. ”</p>
    <p class="author">Sarah Mills, Party Mum</p>
  </section>

  <aside class="call-box abs">
    <small>For any enquiries</small>
    <h3>Call Us Today</h3>
    <div class="phone">555-210-4873</div>
    <span class="btn-line">Get Started now</span>
  </aside>

  <h2 class="welcome-title section-title abs">Welcome to Benny Fairweather</h2>
  <div class="welcome-photo abs" role="img" aria-label="Entertainer with three balloon pigs on his head"></div>
  <div class="welcome-text abs">
    <h2>Sed ut perspiciatis unde omnis iste natus error sit voluptatem accusantium doloremque laudan.</h2>
    <p>Lorem ipsum dolor sit amet, consectetur adipiscing elit, sed do eiusmod tempor incididunt ut labore et dolore magna aliqua enim.</p>
    <p>Ut enim ad minim veniam, quis nostrud exercitation ullamco laboris nisi.</p>
    <span class="btn">Read More</span>
  </div>

  <aside class="news abs">
    <h2 class="section-title">Latest News</h2>
    <div class="news-item"><div class="news-thumb" role="img" aria-label="News photo" style="background:linear-gradient(135deg,#5aa0d8,#2e5fa8)"></div><p><b>Party season</b>Lorem ipsum dolor sit amet consectetur.</p></div>
    <div class="news-item"><div class="news-thumb" role="img" aria-label="News photo" style="background:linear-gradient(135deg,#f5b04a,#e1702a)"></div><p><b>New show dates</b>Sed do eiusmod tempor incididunt ut.</p></div>
    <div class="news-item"><div class="news-thumb" role="img" aria-label="News photo" style="background:linear-gradient(135deg,#f3a0b8,#c84f7a)"></div><p><b>Workshops open</b>Ut enim ad minim veniam quis nostrud.</p></div>
  </aside>

  <section class="services abs">
    <div class="cards">
      <article class="card"><h3>Balloon Shows</h3><div class="card-photo" role="img" aria-label="Child enjoying a balloon show" style="background:linear-gradient(135deg,#f6d54a,#e88a2a)"></div><p>Lorem ipsum dolor sit amet, consectetur adipiscing elit sed do eiusmod.</p><span class="btn">Read More</span></article>
      <article class="card"><h3>Balloon Twisting</h3><div class="card-photo" role="img" aria-label="Entertainer twisting balloons for children" style="background:linear-gradient(135deg,#8fd15a,#e04a3a)"></div><p>Lorem ipsum dolor sit amet, consectetur adipiscing elit sed do eiusmod.</p><span class="btn">Read More</span></article>
      <article class="card"><h3>Balloon Workshops</h3><div class="card-photo" role="img" aria-label="Children at a balloon workshop" style="background:linear-gradient(135deg,#f2a14a,#c9552a)"></div><p>Lorem ipsum dolor sit amet, consectetur adipiscing elit sed do eiusmod.</p><span class="btn">Read More</span></article>
      <article class="card"><h3>Theatre Shows</h3><div class="card-photo" role="img" aria-label="Family theatre show on stage" style="background:linear-gradient(135deg,#f4a7c0,#d9607f)"></div><p>Lorem ipsum dolor sit amet, consectetur adipiscing elit sed do eiusmod.</p><span class="btn">Read More</span></article>
    </div>
  </section>

  <section class="connect abs">
    <h2>Connect With Benny Fairweather</h2>
    <p>Sed ut perspiciatis unde omnis iste natus error sit voluptatem accusantium doloremque laudantium totam rem aperiam.</p>
    <form class="signup">
      <span class="icon"><svg width="12" height="9" viewBox="0 0 12 9"><rect x="0.5" y="0.5" width="11" height="8" fill="none" stroke="#fff"/><path d="M0.5 0.5 L6 5 L11.5 0.5" fill="none" stroke="#fff"/></svg></span>
      <span class="field">Enter email address</span>
      <span class="go">Go</span>
    </form>
  </section>

  <footer class="site-footer abs">
    <svg width="683" height="20" viewBox="0 0 683 20"><path d="M0 20 Q341 0 683 20 Z" fill="#f37122"/></svg>
    <div class="social"><span></span><span></span><span></span><span></span></div>
    <div class="footer-links">Home | Balloon Shows | Balloon Twisting | Theatre | Reviews | Contact</div>
    <div class="copyright">Tel: 555-210-4873 · © Benny Fairweather. All rights reserved.</div>
  </footer>

</div>
</body>
</html>
```